Striking new Advert required for Commercial Real Estate Agency

We need a a NEW newspaper advertisement for the marketing of a large commercial property (a Backpackers lodge)

Dimensions are to be width of 101mm and height of 100mm (10cms)

Our key design statement for this advert is clean, modern and minimalist design, with accents of 'HOT PINK' colour to remove it from looking too boring, perhaps in the area of the contact icons. The heirachy of the advert is outlined in the attached ADVERTISEMENT TEXT FILE.

Our company name is THE HARBOURLINE COLLECTIVE, and we want our brand to appear professional yet classy in it's design style (sort of like an advertising or design agency)

We have two logo options below, one more square in its layout (which we prefer) and the other more rectangular, which may be better suited for the layout. We are not adverse to the logo being reversed (white text on black), along with other key element areas such as the main advert heading and the "FOR SALE" part, and think this would be a good option.
There are two photos attached to be included in the advert.

We have attached an example of an old advert that we did, which we DID NOT LIKE, and which was for a smaller width than the one we need (it is only 65% of the width of this one). WE have also atached a file showing layout of some of our competitors adverts, which we dont think are too good either.

We are really open for ideas, but have time pressures, so please come back with any questions as soon as you can, if needed.

Thank you
Updates

Thank you for the great and diverse designs. There are a few standout options, but one style that we prefer most.

Target Market(s)

We are wanting this newspaper advertisement to attract interest from real estat e developers, investors and motel/lodge owners, along with other high nett worth individuals

Industry/Entity Type

Real Estate

Font styles to use
Serif
Sans Serif

Colors
1b1b1b
a54499
474747
fbfbfb

Requirements
Must have
• Clean modern look, predominantly monochromatic or black and white, with the hot pink accent somewhere, as mentioned above.
• All the contents of the TEXT provided, perhaps with additional space to add a little more if needed, Please advise if you think we dont have enough space for all of the TEXT
Should not have
• Script like fonts
• Cartoonish characters
• a 'cheap' look

```html
<!DOCTYPE html>
<html lang="en">
<head>
<meta charset="utf-8">
<title>For Sale – Mount Victoria Land Grab</title>
<link rel="stylesheet" href="https://fonts.googleapis.com/css2?family=Montserrat:wght@800&family=Source+Sans+3:wght@400;600&display=swap">
<style>
  :root {
    --ink: #1b1b1b;
    --pink: #a54499;
    --grey-text: #474747;
    --paper: #fbfbfb;
    --backdrop: #cdcdcd;
    --photo-sky: #8fb3d9;
    --photo-house: #d9dde2;
    --photo-roofs: #8a8f7a;
    --photo-green: #6f8c4a;
  }
  * { box-sizing: border-box; margin: 0; padding: 0; }
  html, body { width: 1200px; height: 903px; overflow: hidden; }
  body {
    background: var(--backdrop);
    font-family: "Source Sans 3", "Myriad Pro", sans-serif;
    position: relative;
  }
  .advert {
    position: absolute;
    left: 286px; top: 141px;
    width: 629px; height: 622px;
    background: var(--paper);
    color: var(--ink);
  }
  .headline {
    position: absolute; left: 34px; top: 22px;
    font-family: "Montserrat", "Arial Black", sans-serif;
    font-weight: 800; font-size: 49px; line-height: 1;
    letter-spacing: 0.5px; color: var(--ink);
  }
  .tagline {
    position: absolute; right: 35px; top: 47px;
    font-size: 19.5px; color: var(--grey-text); line-height: 1;
  }
  .photo { position: absolute; top: 75px; height: 178px; }
  .photo--street {
    left: 30px; width: 280px;
    background: linear-gradient(180deg, var(--photo-sky) 0%, var(--photo-house) 45%, #c6cbd0 75%, var(--photo-green) 100%);
  }
  .photo--aerial {
    left: 316px; width: 282px;
    background: linear-gradient(180deg, #b9c0c4 0%, var(--photo-roofs) 40%, #a9a79d 70%, var(--photo-green) 100%);
  }
  .address-band {
    position: absolute; left: 30px; top: 256px;
    width: 568px; height: 40px;
    background: var(--ink); color: #fff;
    display: flex; align-items: center; justify-content: center;
    font-size: 21px; letter-spacing: -0.2px;
  }
  .details {
    position: absolute; left: 30px; top: 302px; width: 568px;
    font-size: 17px; line-height: 21px; color: var(--ink);
  }
  .details .intro { color: var(--grey-text); }
  .details .lead { color: var(--pink); margin-top: 6px; }
  .features { list-style: none; margin-top: 0; }
  .features li {
    position: relative; padding-left: 24px;
    text-align: justify; margin-bottom: 5px;
    color: var(--grey-text);
  }
  .features li::before {
    content: ""; position: absolute; left: 5px; top: 8px;
    width: 7px; height: 7px; border-radius: 50%; background: var(--pink);
  }
  .features sup { font-size: 10px; line-height: 0; }
  .tender {
    text-align: center; color: var(--pink);
    font-weight: 600; font-size: 17px; margin-top: 1px;
  }
  .contact-bar {
    position: absolute; left: 0; top: 536px;
    width: 629px; height: 86px;
    background: var(--ink); color: #fff;
  }
  .agent-name {
    position: absolute; left: 33px; top: 5px;
    font-weight: 600; font-size: 18.5px;
  }
  .contact-line {
    position: absolute; display: flex; align-items: center; gap: 8px;
    font-size: 16.5px; line-height: 1;
  }
  .contact-line svg { width: 13px; height: 13px; flex: none; }
  .contact-line--office { left: 32px; top: 35px; }
  .contact-line--mobile { left: 32px; top: 57px; }
  .contact-line--email { left: 193px; top: 33px; }
  .contact-line--web { left: 193px; top: 55px; }
  .brand-name {
    position: absolute; left: 478px; top: 18px;
    font-size: 13px; line-height: 15px; letter-spacing: 1px;
    color: #fff; text-transform: uppercase;
  }
</style>
</head>
<body>
  <article class="advert">
    <h1 class="headline">FOR SALE</h1>
    <p class="tagline">Mount Victoria Land Grab</p>

    <div class="photo photo--street" role="img" aria-label="Photo of the two-storey white weatherboard lodge with balconies and fire escape"></div>
    <div class="photo photo--aerial" role="img" aria-label="Aerial photo of the lodge and surrounding Mount Victoria neighbourhood"></div>

    <div class="address-band">Marlowe’s Lodge, 48 Kestrel Street, Mount Victoria</div>

    <section class="details">
      <p class="intro">This Old Beauty has served many, and is now ripe for development.</p>
      <p class="lead">One of Mt Vic’s largest land areas, now offered with vacant possession, with key details being:</p>
      <ul class="features">
        <li>Large Land area of 2076m<sup>2</sup> with elevated sunny position and great outlook + access from Alder Street</li>
        <li>Existing Backpackers Lodge of 970m<sup>2</sup> providing multiple rooms with amenity areas</li>
        <li>Four adjacent sites also available, taking total land area to 4452m<sup>2</sup>, an unprecedented Land Offering in this popular cuity fringe location</li>
      </ul>
      <p class="tender">NOW SELLING BY CLOSED TENDER</p>
    </section>

    <footer class="contact-bar">
      <p class="agent-name">Daniel Whitmore</p>
      <p class="contact-line contact-line--office">
        <svg viewBox="0 0 16 16" aria-hidden="true"><path fill="var(--pink)" d="M3.6 1.2l2.3 2.9-1.3 1.6c.9 2 2.5 3.6 4.5 4.5l1.6-1.3 2.9 2.3-1.3 2.6C7 13.5 2.5 9 1.2 2.5z"/></svg>
        (04) 555 0182
      </p>
      <p class="contact-line contact-line--mobile">
        <svg viewBox="0 0 16 16" aria-hidden="true"><rect x="4" y="1" width="8" height="14" rx="1.5" fill="none" stroke="var(--pink)" stroke-width="1.6"/><circle cx="8" cy="12.3" r="1" fill="var(--pink)"/></svg>
        (021) 555 0347
      </p>
      <p class="contact-line contact-line--email">
        <svg viewBox="0 0 16 16" aria-hidden="true"><rect x="1.5" y="4" width="13" height="8.5" fill="var(--pink)"/><path d="M1.5 4l6.5 5 6.5-5" fill="none" stroke="var(--ink)" stroke-width="1.1"/></svg>
        daniel@harbourlinecollective.co.nz
      </p>
      <p class="contact-line contact-line--web">
        <svg viewBox="0 0 16 16" aria-hidden="true"><g fill="none" stroke="var(--pink)" stroke-width="1.3"><circle cx="8" cy="8" r="6.3"/><ellipse cx="8" cy="8" rx="2.8" ry="6.3"/><path d="M1.7 8h12.6M2.8 4.8h10.4M2.8 11.2h10.4"/></g></svg>
        www.harbourlinecollective.co.nz
      </p>
      <p class="brand-name">The<br>Harbourline<br>Collective</p>
    </footer>
  </article>
</body>
</html>
```